Hello my Name is Elias Moreno. I buy and sell vintage comic books, you can refer to my instragram page qpkz.comics to get ideas and inspiration. For the front of the card I would like my company logo QPKZ Comics with a yellow and black background with the bat signal or bat emblem like on my IG page and with my info Elias Moreno as the Owner and address/ phone number, PO Box 617283, Miami, FL 33827, 305-482-6170 and that I buy and sell comics & collectables . Also feel free to be open to other ideas if you want. Im not stuck on one design. For the back of the card I would like for it to say follow me on Instagram QPKZ.Comics with the ig emblem. Also would like the card to be vertical if possible. Thanks

```html
<!DOCTYPE html>
<html lang="en">
<head>
<meta charset="utf-8">
<title>QPKZ Comics – Business Card</title>
<link rel="stylesheet" href="https://fonts.googleapis.com/css2?family=Signika:wght@400;600;700&family=IM+Fell+English+SC&display=swap">
<style>
  :root {
    --card-black: #0b0b0b;
    --brand-yellow: #f7c823;
    --text-white: #f4f4f4;
    --page-bg: #d9d6d0;
  }
  html, body {
    margin: 0;
    padding: 0;
    width: 1200px;
    height: 950px;
    overflow: hidden;
    background: var(--page-bg);
  }
  .canvas {
    position: relative;
    width: 1200px;
    height: 950px;
    display: flex;
    align-items: center;
    justify-content: center;
  }
  .card {
    position: relative;
    width: 460px;
    height: 760px;
    background: var(--card-black);
    border-radius: 14px 14px 200px 200px / 14px 14px 120px 120px;
    overflow: hidden;
    box-shadow: 0 18px 40px rgba(0,0,0,0.25);
  }
  .card-details {
    position: absolute;
    top: 48px;
    right: 40px;
    text-align: right;
    font-family: "Signika", sans-serif;
    color: var(--text-white);
    font-size: 23px;
    line-height: 1.38;
  }
  .owner-name {
    font-weight: 700;
    font-size: 31px;
    color: var(--brand-yellow);
    letter-spacing: 1px;
    text-transform: uppercase;
    margin: 0;
  }
  .owner-title { margin: 0 0 4px; }
  .contact-line { margin: 0; }
  .label { color: var(--brand-yellow); font-weight: 600; }
  .tagline {
    margin: 18px 0 0;
    font-family: "IM Fell English SC", serif;
    color: var(--brand-yellow);
    font-size: 30px;
    line-height: 1.15;
    text-transform: uppercase;
  }
  .brand-field {
    position: absolute;
    left: 0;
    bottom: 0;
    width: 460px;
    height: 390px;
  }
  .brand-name {
    position: absolute;
    left: 70px;
    width: 260px;
    top: 598px;
    text-align: center;
    font-family: "Signika", sans-serif;
    font-weight: 700;
    font-size: 34px;
    line-height: 44px;
    color: var(--text-white);
    letter-spacing: 1px;
    margin: 0;
  }
  .social-handle {
    position: absolute;
    right: 24px;
    top: 512px;
    display: flex;
    align-items: center;
    gap: 8px;
    font-family: "Signika", sans-serif;
    font-weight: 600;
    font-size: 17px;
    line-height: 1;
    color: var(--card-black);
  }
  .social-dot {
    width: 14px;
    height: 14px;
    border-radius: 50%;
    background: var(--card-black);
    flex: none;
  }
</style>
</head>
<body>
<main class="canvas">
  <article class="card">
    <svg class="brand-field" viewBox="0 0 460 390" aria-hidden="true">
      <ellipse cx="230" cy="250" rx="300" ry="200" fill="var(--brand-yellow)"/>
      <circle cx="200" cy="250" r="130" fill="var(--card-black)"/>
    </svg>

    <section class="card-details">
      <h1 class="owner-name">Elias Moreno</h1>
      <p class="owner-title">Owner</p>
      <p class="contact-line"><span class="label">P:</span> 305-482-6170</p>
      <p class="contact-line">elias@qpkzcomics.com</p>
      <p class="contact-line">www.qpkzcomics.com</p>
      <p class="contact-line">PO Box 617283, Miami, FL 33827</p>
      <p class="tagline">Buy &amp; Sell Comics<br>&amp; Collectables</p>
    </section>

    <p class="brand-name">QPKZ Comics</p>

    <div class="social-handle">
      <span class="social-dot"></span>
      <span>qpkz.comics</span>
    </div>
  </article>
</main>
</body>
</html>
```